KVR - Redesign (PSD Files Only)

Requirements for the site:

1. We need our logo recreated, please use the same design and change colors to work on a white background

2. The site is a "Wizard" based site, that takes the customer through the process of creating a unique web presence that suits there needs

3.Colors Needed - Main "Dark Blue" Secondary = "Dark Grey" -Other = "Light Grey and White"

4.We need a CRISP CLEAN DESIGN, simple design

5.Wireframes are a general layout and may be modified by you to enhance the design

6. We want a complete web 5.0 look with big buttons and text boxes

7.The more personality the better

8. Current Site brightpolehub.example

9.See attachments for wireframes

10. Designer should deliver PSD files, no coding is required

11. The portfolio wireframe, should look like the design of the artflockly portfolio template
Updates

KEEP IT SIMPLE.,.....

We like the quillmark scaffold style of designs

```html
<!DOCTYPE html>
<html lang="en">
<head>
<meta charset="utf-8">
<title>KVR – All Steps Process</title>
<link href="https://fonts.googleapis.com/css2?family=Dosis:wght@300;400;500;700&family=Open+Sans:ital,wght@0,400;1,400&display=swap" rel="stylesheet">
<style>
:root{
  --navy:#003a66;
  --nav-active:#1f4e7a;
  --topbar:#1b1b1b;
  --page-bg:#d5d5d5;
  --panel:#ffffff;
  --track:#e5e5e5;
  --track-alt:#c2c2c2;
  --footer:#1e1e1e;
  --footer-band:#191919;
  --orange-top:#ff9a1f;
  --orange-bottom:#ff7a00;
  --text:#222;
  --muted:#999;
}
*{margin:0;padding:0;box-sizing:border-box}
html,body{width:1200px;height:1053px;overflow:hidden}
body{position:relative;background:var(--page-bg);font-family:'Open Sans',sans-serif;color:var(--text)}
.topbar{position:absolute;left:0;top:0;width:1200px;height:24px;background:var(--topbar)}
.hero{position:absolute;left:0;top:24px;width:1200px;height:150px;
  background:radial-gradient(ellipse at 50% 60%,#0a5a8c 0%,#023c6b 45%,#002d57 100%)}
.nav{position:absolute;left:129px;top:0;width:942px;height:46px;background:var(--topbar);font-family:'Dosis',sans-serif}
.logo{position:absolute;left:20px;top:10px;color:#fff;font-weight:700;font-size:20px;letter-spacing:1px}
.menu{position:absolute;left:96px;top:0;display:flex;height:46px}
.menu a{color:#fff;text-decoration:none;font-size:20px;padding:0 10px;line-height:46px}
.menu a.active{background:var(--nav-active);padding:0 13px}
.social-top{position:absolute;left:575px;top:10px;display:flex;gap:8px}
.soc{width:26px;height:26px;border-radius:50%;background:#fff;color:#1b1b1b;font-family:'Open Sans',sans-serif;font-size:9px;font-weight:700;display:flex;align-items:center;justify-content:center}
.phone-top{position:absolute;right:16px;top:0;line-height:46px;color:#fff;font-size:25px;font-weight:300;display:flex;align-items:center;gap:6px}
.title{position:absolute;left:0;top:88px;width:1200px;text-align:center;color:#fff;font-family:'Dosis',sans-serif;font-weight:700;font-size:34px}
.title .dots{display:inline-block;width:48px;border-top:3px dotted #fff;vertical-align:middle;margin:0 16px}
.panel{position:absolute;left:129px;top:174px;width:942px;height:650px;background:var(--panel);border-left:1px solid #bbb;border-right:1px solid #bbb}
.notch{position:absolute;left:588px;top:162px;width:0;height:0;border-left:12px solid transparent;border-right:12px solid transparent;border-bottom:12px solid #fff}
.crumbs{position:absolute;left:42px;top:18px;font-size:12px;color:var(--navy)}
.crumbs .sep{margin:0 8px;font-weight:700}
.crumbs .cur{color:var(--muted)}
.crumb-line{position:absolute;left:0;top:51px;width:940px;border-top:1px solid #e4e4e4}
.option{position:absolute;left:0;width:940px;text-align:center;font-family:'Dosis',sans-serif;font-weight:400;font-size:35px;line-height:36px;color:#111}
.steps{position:absolute;left:0;top:0}
.step-label{font-family:'Open Sans',sans-serif;font-size:12.5px;fill:#111;text-anchor:middle}
.info{position:absolute;left:25px;top:559px;width:891px;height:51px;background:var(--navy);border:1px solid #0b4f80;display:flex;align-items:center;color:#fff;font-style:italic;font-size:15.5px}
.info .i{width:28px;height:28px;border-radius:50%;background:#fff;color:var(--navy);font-weight:700;font-family:Georgia,serif;font-size:18px;display:flex;align-items:center;justify-content:center;margin:0 12px 0 16px}
.footer{position:absolute;left:0;top:824px;width:1200px;height:229px;background:var(--footer)}
.footer-band{position:absolute;left:129px;top:123px;width:949px;height:54px;background:var(--footer-band)}
.footer-links{position:absolute;left:129px;top:43px;color:#fff;font-size:12.5px;line-height:19px}
.footer-links .dot{margin:0 6px}
.social-foot{position:absolute;left:498px;top:44px;display:flex;gap:8px}
.social-foot .soc{width:38px;height:38px;font-size:11px}
.phone-foot{position:absolute;left:498px;top:84px;color:#fff;font-family:'Dosis',sans-serif;font-weight:300;font-size:25px;display:flex;align-items:center;gap:4px}
.cta{position:absolute;left:828px;top:38px;width:243px;height:55px;background:linear-gradient(var(--orange-top),var(--orange-bottom));color:#fff;font-family:'Dosis',sans-serif;font-weight:700;font-size:27px;display:flex;align-items:center;justify-content:center}
.badge{position:absolute;left:129px;top:124px;width:156px;height:53px;background:#fff;display:flex}
.badge .mark{width:54px;height:53px;background:#3b6fd3}
</style>
</head>
<body>
<div class="topbar"></div>
<header class="hero"></header>
<nav class="nav">
  <div class="logo">KVR</div>
  <div class="menu">
    <a href="#">Home</a><a href="#" class="active">About Us</a><a href="#">Portfolio</a><a href="#">Contact Us</a>
  </div>
  <div class="social-top"><div class="soc">Sn</div><div class="soc">Pk</div><div class="soc">Vu</div><div class="soc">Qr</div></div>
  <div class="phone-top">
    <svg width="16" height="18" viewBox="0 0 16 18"><path d="M4 1 L7 5 L5 7 Q7 11 10 13 L12 11 L15 14 L13 17 Q6 16 2 8 Q1 4 4 1Z" fill="#fff"/></svg>
    <span style="font-family:'Dosis',sans-serif">1800-555-0142</span>
  </div>
</nav>
<h1 class="title"><span class="dots"></span>All Steps Process<span class="dots"></span></h1>
<div class="notch"></div>

<main class="panel">
  <div class="crumbs">Level 1<span class="sep">»</span>Level 2<span class="sep">»</span>Level 3<span class="sep">»</span><span class="cur">Level 4</span></div>
  <div class="crumb-line"></div>

  <svg class="steps" width="940" height="560" viewBox="0 0 940 560">
    <defs>
      <g id="needle">
        <polygon points="0,-24 3,0 0,4 -3,0" fill="#000"/>
        <circle r="4.5" fill="#a8c2de"/><circle r="2.2" fill="#0b1e33"/>
      </g>
    </defs>
    <g transform="translate(714,49)">
      <circle r="44" fill="#fff"/>
      <circle r="31" fill="none" stroke="var(--track)" stroke-width="13"/>
      <circle r="31" fill="none" stroke="var(--navy)" stroke-width="13" stroke-dasharray="24.35 200" transform="rotate(-90)"/>
      <use href="#needle"/>
    </g>

    <g>
      <text class="step-label" x="157" y="153">Step1</text>
      <text class="step-label" x="243" y="153">Step2</text>
      <text class="step-label" x="328" y="153">Step3</text>
      <text class="step-label" x="414" y="153">Step4</text>
      <text class="step-label" x="517" y="153">Step5</text>
      <text class="step-label" x="595" y="153">Step6</text>
      <text class="step-label" x="677" y="153">Step7</text>
      <text class="step-label" x="776" y="153">Final Step</text>
    </g>
    <g stroke-width="13" fill="none">
      <g transform="translate(157,216)"><circle r="31" stroke="var(--track)"/><circle r="31" stroke="var(--navy)" stroke-dasharray="24.35 200" transform="rotate(-90)"/><use href="#needle" transform="rotate(45)"/></g>
      <g transform="translate(243,216)"><circle r="31" stroke="var(--track)"/><circle r="31" stroke="var(--navy)" stroke-dasharray="48.7 200" transform="rotate(-90)"/><use href="#needle" transform="rotate(90)"/></g>
      <g transform="translate(328,216)"><circle r="31" stroke="var(--track)"/><circle r="31" stroke="var(--navy)" stroke-dasharray="73.05 200" transform="rotate(-90)"/><use href="#needle" transform="rotate(135)"/></g>
      <g transform="translate(414,216)"><circle r="31" stroke="var(--track)"/><circle r="31" stroke="var(--navy)" stroke-dasharray="97.4 200" transform="rotate(-90)"/><use href="#needle" transform="rotate(180)"/></g>
      <g transform="translate(499,216)"><circle r="31" stroke="var(--track)"/><circle r="31" stroke="var(--navy)" stroke-dasharray="121.75 200" transform="rotate(-90)"/><use href="#needle" transform="rotate(225)"/></g>
      <g transform="translate(594,216)"><circle r="31" stroke="var(--track)"/><circle r="31" stroke="var(--navy)" stroke-dasharray="146.1 200" transform="rotate(-90)"/><use href="#needle" transform="rotate(270)"/></g>
      <g transform="translate(679,216)"><circle r="31" stroke="var(--track)"/><circle r="31" stroke="var(--navy)" stroke-dasharray="170.45 200" transform="rotate(-90)"/><use href="#needle" transform="rotate(315)"/></g>
      <g transform="translate(774,216)"><circle r="31" stroke="var(--navy)"/><use href="#needle"/></g>
    </g>

    <g>
      <text class="step-label" x="160" y="386">Step1</text>
      <text class="step-label" x="249" y="386">Step2</text>
      <text class="step-label" x="339" y="386">Step3</text>
      <text class="step-label" x="426" y="386">Step4</text>
      <text class="step-label" x="517" y="386">Step5</text>
      <text class="step-label" x="605" y="386">Step6</text>
      <text class="step-label" x="695" y="386">Step7</text>
      <text class="step-label" x="785" y="386">Final Step</text>
    </g>
    <g stroke-width="13" fill="none">
      <g transform="translate(160,439)"><circle r="31" stroke="var(--track-alt)"/><circle r="31" stroke="var(--navy)" stroke-dasharray="24.35 200" transform="rotate(-90)"/><use href="#needle" transform="rotate(45)"/></g>
      <g transform="translate(249,439)"><circle r="31" stroke="var(--track-alt)"/><circle r="31" stroke="var(--navy)" stroke-dasharray="48.7 200" transform="rotate(-90)"/><use href="#needle" transform="rotate(90)"/></g>
      <g transform="translate(339,439)"><circle r="31" stroke="var(--track-alt)"/><circle r="31" stroke="var(--navy)" stroke-dasharray="73.05 200" transform="rotate(-90)"/><use href="#needle" transform="rotate(135)"/></g>
      <g transform="translate(426,439)"><circle r="31" stroke="var(--track-alt)"/><circle r="31" stroke="var(--navy)" stroke-dasharray="97.4 200" transform="rotate(-90)"/><use href="#needle" transform="rotate(180)"/></g>
      <g transform="translate(513,439)"><circle r="31" stroke="var(--track-alt)"/><circle r="31" stroke="var(--navy)" stroke-dasharray="121.75 200" transform="rotate(-90)"/><use href="#needle" transform="rotate(225)"/></g>
      <g transform="translate(606,439)"><circle r="31" stroke="var(--track-alt)"/><circle r="31" stroke="var(--navy)" stroke-dasharray="146.1 200" transform="rotate(-90)"/><use href="#needle" transform="rotate(270)"/></g>
      <g transform="translate(695,439)"><circle r="31" stroke="var(--track-alt)"/><circle r="31" stroke="var(--navy)" stroke-dasharray="170.45 200" transform="rotate(-90)"/><use href="#needle" transform="rotate(315)"/></g>
      <g transform="translate(786,439)"><circle r="31" stroke="var(--navy)"/><use href="#needle"/></g>
    </g>
  </svg>

  <h2 class="option" style="top:82px">Option 1</h2>
  <h2 class="option" style="top:314px">Option 2</h2>

  <div class="info"><span class="i">i</span>As your full service marketing partner, we will deliver and end to end marketing solution for your business.</div>
</main>

<footer class="footer">
  <div class="footer-band"></div>
  <div class="footer-links">
    <div>Home<span class="dot">.</span>About Us<span class="dot">.</span>Portfolio<span class="dot">.</span>Contact Us</div>
    <div>Copyright © 2014 Brightpole Studios Inc - All Right Reserved</div>
    <div>www.brightpolehub.example</div>
  </div>
  <div class="social-foot"><div class="soc">Sn</div><div class="soc">Pk</div><div class="soc">Vu</div><div class="soc">Qr</div></div>
  <div class="phone-foot">
    <svg width="16" height="20" viewBox="0 0 16 18"><path d="M4 1 L7 5 L5 7 Q7 11 10 13 L12 11 L15 14 L13 17 Q6 16 2 8 Q1 4 4 1Z" fill="#fff"/></svg>
    1800-555-0142
  </div>
  <div class="cta">Request Consultant</div>
  <div class="badge" role="img" aria-label="Partner badge"><div class="mark"></div></div>
</footer>
</body>
</html>
```